we are an outdoor outlet in a country club that has a variety of outlets. The Club is called Meadowlark and is located in Cairo, Egypt. This garden menu will include cuisines from the Mediterranean, Asia and Texmex. we need a menu that is colorful and would fit an A3 size, back and front are to be used. Attached is the old menu currently in use (Garden Menu 2012.pdf is just for reference) and the new menu text for you to use is under the name Garden Menu Fall 2013
thank you.
Updates
Logo files have been uploaded for this project
Industry/Entity Type
Club
Look and feel
Each slider illustrates characteristics of the customer's brand and the style your logo design should communicate.

```html
<!DOCTYPE html>
<html lang="en">
<head>
<meta charset="utf-8">
<title>Meadowlark Garden Menu</title>
<link href="https://fonts.googleapis.com/css2?family=Didact+Gothic&family=Great+Vibes&family=Parisienne&display=swap" rel="stylesheet">
<style>
:root{
  --lime:#c9dc2f;
  --beige:#e6e2d7;
  --paper:#ffffff;
  --berry:#b8194f;
  --rose:#d8457a;
  --blue:#2f6d9c;
  --olive:#8a9a1c;
  --ink:#4a2b2b;
  --soft:#6b5a56;
}
*{box-sizing:border-box;margin:0;padding:0}
html,body{width:1000px;height:1200px;overflow:hidden}
body{background:var(--lime);position:relative;font-family:"Didact Gothic",sans-serif;color:var(--ink)}
.panel{position:absolute;background:var(--paper);overflow:hidden}
.panel--front{left:22px;top:22px;width:958px;height:568px}
.panel--back{left:160px;top:605px;width:818px;height:577px}
.band{position:absolute;top:0;bottom:0;background:var(--beige)}
.abs{position:absolute}
.art{position:absolute;border-radius:6px}
.title-script{font-family:"Great Vibes",cursive;color:var(--berry);font-size:30px}
.corner{position:absolute;text-align:center;font-family:"Parisienne",cursive;color:var(--ink);font-size:22px}
.corner::after{content:"";display:block;margin:2px auto 0;width:200px;height:2px;background:var(--olive);border-radius:2px}
.sec{position:absolute;text-align:center;font-size:14px;font-weight:bold;letter-spacing:.3px}
.sec--berry{color:var(--berry)}
.sec--blue{color:var(--blue)}
.sec--olive{color:var(--olive)}
.list{position:absolute}
.item{position:relative;padding-right:44px;margin-bottom:6px}
.item .name{font-family:"Parisienne",cursive;font-size:13px;color:var(--ink);line-height:1.1}
.item .desc{font-size:6.3px;color:var(--soft);line-height:1.35}
.item--fixed{height:29px;margin-bottom:0}
.item--fixed .desc{line-height:1.2}
.price{position:absolute;right:0;bottom:0;font-size:5.8px;color:var(--soft);white-space:nowrap}
.bul{position:relative;padding-left:9px;padding-right:44px;font-size:6.3px;color:var(--soft);height:12.4px;line-height:12.4px;white-space:nowrap}
.bul::before{content:"";position:absolute;left:0;top:4px;width:5px;height:5px;border-radius:50%;background:var(--rose)}
.bul .price{bottom:2px}
.note{position:absolute;font-size:7px;color:var(--berry);white-space:nowrap}
.big-script{font-family:"Parisienne",cursive;font-size:17px;line-height:1.2;color:var(--ink)}
.small-corner{position:absolute;font-family:"Parisienne",cursive;font-size:11px;color:var(--ink)}
.brand{position:absolute;text-align:center;font-family:"Didact Gothic",sans-serif;color:var(--ink)}
.dessert{position:relative;padding-left:9px;padding-right:40px;font-size:6.6px;color:var(--soft);height:24px;line-height:1.3;display:flex;align-items:center}
.dessert::before{content:"";position:absolute;left:0;top:50%;margin-top:-3px;width:5px;height:5px;border-radius:50%;background:var(--rose)}
.dessert .price{bottom:auto;top:50%;margin-top:-4px}
</style>
</head>
<body>

<section class="panel panel--front">
  <div class="band" style="left:0;width:198px"></div>
  <div class="abs title-script" style="left:18px;top:30px">Garden Menu</div>
  <div class="brand" style="left:40px;top:135px;width:120px;font-size:17px">Meadowlark</div>
  <div class="art" role="img" aria-label="Botanical illustration of climbing stems, leaves and pink blossoms" style="left:10px;top:210px;width:180px;height:350px;background:linear-gradient(160deg,#dcd7c8 0%,#b9c36b 45%,#c9617f 100%);opacity:.75"></div>
  <div class="art" role="img" aria-label="Olive branch illustration" style="left:815px;top:0;width:143px;height:70px;background:linear-gradient(120deg,#e8ebd8,#c7cf97);opacity:.7"></div>

  <div class="corner" style="left:218px;top:36px;width:260px">Mediterranean Corner</div>
  <div class="sec sec--berry" style="left:218px;top:76px;width:260px">Soups</div>
  <div class="list" style="left:218px;top:96px;width:245px">
    <div class="item"><div class="name">Tomato Basil.</div><div class="desc">Simmered tomato soup finished with fresh basil and cream.</div><span class="price">EL 00.00</span></div>
    <div class="item"><div class="name">Chicken Cream.</div><div class="desc">Chicken broth with roasted chicken cubes, pine nuts, and cream.</div><span class="price">EL 00.00</span></div>
    <div class="item"><div class="name">Moroccan Harira.</div><div class="desc">Vegetable broth with fresh tomato, chickpeas, lentil, cilantro and diced lamb.</div><span class="price">EL 00.00</span></div>
  </div>
  <div class="sec sec--berry" style="left:218px;top:193px;width:260px">Appetizers</div>
  <div class="list" style="left:212px;top:214px;width:266px">
    <div class="bul">Salmon tartare seasoned with lemon juice, garlic, and crushed black pepper.<span class="price">EL 00.00</span></div>
    <div class="bul">Roasted eggplant rolls with herbed ricotta cheese and pine nuts.<span class="price">EL 00.00</span></div>
    <div class="bul">Falafel in mini pita served with tehina and oriental salsa.<span class="price">EL 00.00</span></div>
    <div class="bul">Mankousha with thyme and olive oil.<span class="price">EL 00.00</span></div>
    <div class="bul">Fried kobeba with minced meat, spices, and pine nuts.<span class="price">EL 00.00</span></div>
    <div class="bul">Fried calamari a la Romana served with aioli.<span class="price">EL 00.00</span></div>
    <div class="bul">Sambousses with herbed white cheese and mint.<span class="price">EL 00.00</span></div>
    <div class="bul">Oriental sausage sauteed with garlic and onion.<span class="price">EL 00.00</span></div>
    <div class="bul">Mini vine leaves with a yoghurt dip.<span class="price">EL 00.00</span></div>
    <div class="bul">Fatoush with a pomegranate syrup dressing.<span class="price">EL 00.00</span></div>
    <div class="bul">Hummus seasoned with lemon juice, garlic, and olive oil.<span class="price">EL 00.00</span></div>
    <div class="bul">White cheese with diced tomato, thyme, and olive oil.<span class="price">EL 00.00</span></div>
    <div class="bul">Tehina seasoned with cumin, lemon juice, and garlic.<span class="price">EL 00.00</span></div>
  </div>
  <div class="sec sec--berry" style="left:218px;top:396px;width:260px">Salads</div>
  <div class="list" style="left:218px;top:416px;width:260px">
    <div class="item"><div class="name">Caprese.</div><div class="desc">Buffalo mozzarella and sliced tomato with a balsamic vinaigrette.</div><span class="price">EL 00.00</span></div>
    <div class="item"><div class="name">Rocket Apple.</div><div class="desc">Rocket leaves with gorgonzola, croutons, and strawberry vinaigrette.</div><span class="price">EL 00.00</span></div>
    <div class="item"><div class="name">French Riviera Nicoise.</div><div class="desc">Lettuce, egg, tomato, tuna, olives, onion, celery, radish, bell pepper in a French vinaigrette.</div><span class="price">EL 00.00</span></div>
    <div class="item"><div class="name">Fatto.</div><div class="desc">Mixed greens with crab sticks, mushroom, corn, cherry tomato in a mango vinaigrette.</div><span class="price">EL 00.00</span></div>
  </div>

  <svg class="abs" style="left:488px;top:0" width="14" height="568" viewBox="0 0 14 568" aria-hidden="true">
    <line x1="7" y1="0" x2="7" y2="568" stroke="#d8457a" stroke-width="1"/>
    <line x1="3" y1="0" x2="3" y2="568" stroke="#e8a9bd" stroke-width=".5"/>
    <line x1="11" y1="0" x2="11" y2="568" stroke="#e8a9bd" stroke-width=".5"/>
  </svg>

  <div class="sec sec--blue" style="left:540px;top:38px;width:240px">Pizza &amp; Pasta</div>
  <div class="abs big-script" style="left:532px;top:56px">Lasagna<br>Pizza Margarita<br>Create your own pasta</div>
  <div class="note" style="left:678px;top:92px">{ Choose your toppings }</div>
  <div class="abs" style="left:527px;top:121px;font-size:6.5px;color:var(--soft);white-space:nowrap"><b style="color:var(--blue)">Sauces</b> Napolitana, Bolognese, Alfredo &nbsp;&nbsp;<b style="color:var(--blue)">Type</b> Spaghetti, Tagliatelle, Penne</div>
  <div class="sec sec--berry" style="left:518px;top:163px;width:60px">Toppings</div>
  <div class="list" style="left:578px;top:144px;width:212px">
    <div class="bul" style="height:19px;line-height:19px">Bell peppers, olives, tomato, onion.<span class="price" style="bottom:5px">EL 00.00</span></div>
    <div class="bul" style="height:19px;line-height:19px">Mushroom, chicken, tuna, pepperoni.<span class="price" style="bottom:5px">EL 00.00</span></div>
    <div class="bul" style="height:19px;line-height:19px">Smoked salmon, shrimps.<span class="price" style="bottom:5px">EL 00.00</span></div>
  </div>
  <div class="sec sec--blue" style="left:540px;top:209px;width:240px">Sandwiches</div>
  <div class="note" style="left:570px;top:236px">{ Served with French fries or a garden salad }</div>
  <div class="list" style="left:513px;top:256px;width:277px">
    <div class="bul" style="height:17px;line-height:17px">Beef or chicken Shawerma.<span class="price" style="bottom:4px">EL 00.00</span></div>
    <div class="bul" style="height:17px;line-height:17px">Grilled kofta.<span class="price" style="bottom:4px">EL 00.00</span></div>
    <div class="bul" style="height:17px;line-height:17px">Greek lamb gyro in pita bread with Tzatziki.<span class="price" style="bottom:4px">EL 00.00</span></div>
    <div class="bul" style="height:17px;line-height:17px">Club sandwich with smoked beef, turkey, egg.<span class="price" style="bottom:4px">EL 00.00</span></div>
  </div>
  <div class="sec sec--berry" style="left:540px;top:336px;width:240px">Main Courses</div>
  <div class="list" style="left:515px;top:356px;width:275px">
    <div class="item item--fixed"><div class="name">Veal Parmeggiana.</div><div class="desc">Breaded veal escalope topped with melted cheese and tomato sauce served with Spaghetti.</div><span class="price">EL 00.00</span></div>
    <div class="item item--fixed"><div class="name">Chicken a la Francaise.</div><div class="desc">Pan fried chicken breast in a mushroom cream sauce with vegetables white rice.</div><span class="price">EL 00.00</span></div>
    <div class="item item--fixed"><div class="name">Grilled Salmon.</div><div class="desc">Salmon steak charcoal grilled with avocado tomato relish and creamy mushroom risotto.</div><span class="price">EL 00.00</span></div>
    <div class="item item--fixed"><div class="name">Moroccan Chicken.</div><div class="desc">Chicken cubes simmered with spices and olives served with tomato rice.</div><span class="price">EL 00.00</span></div>
    <div class="item item--fixed"><div class="name">Filet.</div><div class="desc">Tender fillet grilled to your liking served with mashed potato and creamed spinach.</div><span class="price">EL 00.00</span></div>
  </div>
  <div class="note" style="left:515px;top:508px">{ Choice of sauces: Brown mushroom, Green Peppercorn, Gorgonzola }</div>
  <div class="art" role="img" aria-label="Small olive sprig illustration" style="left:560px;top:530px;width:36px;height:26px;background:linear-gradient(90deg,#b8c15d,#e5e8cf);opacity:.7"></div>
  <div class="small-corner" style="left:602px;top:538px">Mediterranean Corner</div>
</section>

<div class="brand" style="left:860px;top:535px;width:115px;font-size:20px;color:#fff">Meadowlark</div>

<section class="panel panel--back">
  <div class="band" style="left:290px;width:65px"></div>
  <div class="band" style="left:623px;width:195px"></div>
  <div class="art" role="img" aria-label="Bamboo stalks, leaves and pink blossom illustration" style="left:215px;top:0;width:165px;height:577px;background:linear-gradient(180deg,#c8cf7d 0%,#ece9df 30%,#ece9df 80%,#c9617f 100%);opacity:.4"></div>
  <div class="art" role="img" aria-label="Patterned green cactus illustration" style="left:300px;top:320px;width:80px;height:257px;background:linear-gradient(180deg,#b2c040,#a3b233);border-radius:40px 40px 0 0"></div>
  <div class="art" role="img" aria-label="Faint flower outline illustration" style="left:690px;top:10px;width:110px;height:90px;background:radial-gradient(circle,#efece4,transparent 70%)"></div>

  <div class="corner" style="left:20px;top:52px;width:240px">Asian Corner</div>
  <div class="sec sec--berry" style="left:20px;top:104px;width:240px">Salads &amp; Appetizers</div>
  <div class="list" style="left:24px;top:128px;width:245px">
    <div class="item"><div class="name">Chicken Wasabi Salad.</div><div class="desc">Diced chicken with a mayo wasabi dressing on top of shredded lettuce.</div><span class="price">EL 00.00</span></div>
    <div class="item"><div class="name">Chicken Sesame Noodle Salad.</div><div class="desc">Sesame crusted chicken with glass noodles tossed with sweet chili, soy sauce, and lemongrass.</div><span class="price">EL 00.00</span></div>
    <div class="item"><div class="name">Spring rolls.</div><div class="desc">Vegetable spring rolls served with house made sweet and sour dip.</div><span class="price">EL 00.00</span></div>
    <div class="item"><div class="name">Indian Samosa.</div><div class="desc">Fried dough parcels filled with vegetables and spices.</div><span class="price">EL 00.00</span></div>
  </div>
  <div class="sec sec--olive" style="left:20px;top:282px;width:240px">Main Courses</div>
  <div class="list" style="left:24px;top:306px;width:245px">
    <div class="item"><div class="name">Murgh Chicken Makhni.</div><div class="desc">Chicken cubes in a rich creamy tomato sauce seasoned with garam masala.</div><span class="price">EL 00.00</span></div>
    <div class="note" style="position:relative;margin:-3px 0 6px">{ Choice of side: vegetable korma or curd }</div>
    <div class="item"><div class="name">Chicken Tandoori.</div><div class="desc">Grilled chicken cubes with tandoori spices served with basmati rice.</div><span class="price">EL 00.00</span></div>
    <div class="item"><div class="name">Thai Coconut Curry Shrimp.</div><div class="desc">Sauteed shrimp tossed with curry and coconut milk served with jasmine rice.</div><span class="price">EL 00.00</span></div>
    <div class="item"><div class="name">Mongolian Beef.</div><div class="desc">Soy marinated beef with oyster sauce and vegetables served with egg noodles.</div><span class="price">EL 00.00</span></div>
  </div>
  <div class="small-corner" style="left:100px;top:548px">Asian Corner</div>

  <div class="corner" style="left:400px;top:52px;width:210px">Tex Mex</div>
  <div class="sec sec--blue" style="left:395px;top:104px;width:220px">Salads &amp; Appetizers</div>
  <div class="list" style="left:390px;top:128px;width:225px">
    <div class="item"><div class="name">Caesar Salad.</div><div class="desc">Iceberg lettuce with Caesar dressing with grated Parmesan cheese and croutons.</div><span class="price">EL 00.00</span></div>
    <div class="item"><div class="name">Taco salad.</div><div class="desc">Chicken breast, beans, sour cream, guacamole, tomato, corn, lettuce, olives, chives, vinaigrette.</div><span class="price">EL 00.00</span></div>
    <div class="item" style="margin-top:12px"><div class="desc">Nachos topped with chili, melted cheese, beans.</div><span class="price">EL 00.00</span></div>
    <div class="item" style="margin-top:10px"><div class="desc">Chicken Quesadilla served with guacamole, salsa, and sour cream.</div><span class="price">EL 00.00</span></div>
  </div>
  <div class="sec sec--berry" style="left:385px;top:282px;width:235px">Main Courses &amp; Sandwiches</div>
  <div class="list" style="left:390px;top:306px;width:225px">
    <div class="item"><div class="name">Cheeseburger.</div><div class="desc">House made lean beef burger topped with cheddar cheese.</div><span class="price">EL 00.00</span></div>
    <div class="item"><div class="name">Mushroom Burger.</div><div class="desc">Beef burger with sauteed mushroom, caramelized onion, and provolone cheese.</div><span class="price">EL 00.00</span></div>
    <div class="item"><div class="name">Crispy Chicken Wrap.</div><div class="desc">Crisp fried chicken wrap with a ranch dressing.</div><span class="price">EL 00.00</span></div>
    <div class="item"><div class="name">Fajita Chicken, Beef, Combo.</div><div class="desc">Pan seared meat or chicken with onion and bell pepper served with sour cream, guacamole, salsa.</div><span class="price">EL 00.00</span></div>
  </div>
  <div class="small-corner" style="left:478px;top:548px">Tex Mex</div>

  <div class="sec sec--berry" style="left:623px;top:104px;width:195px">Desserts</div>
  <div class="list" style="left:633px;top:130px;width:172px">
    <div class="dessert">Mix Berries Cheesecake.<span class="price">EL 00.00</span></div>
    <div class="dessert">Mixed Berries Granola Yoghurt.<span class="price">EL 00.00</span></div>
    <div class="dessert">Warm Chocolate Fondant.<span class="price">EL 00.00</span></div>
    <div class="dessert">Baked Apple Tart Tatin.<span class="price">EL 00.00</span></div>
    <div class="dessert">Creme Brulee.<span class="price">EL 00.00</span></div>
    <div class="dessert">Chocolate Caramel Cake.<span class="price">EL 00.00</span></div>
    <div class="dessert">Tiramisu.<span class="price">EL 00.00</span></div>
    <div class="dessert">Pumpkin Pie Flan.<span class="price">EL 00.00</span></div>
    <div class="dessert">Ice Cream by Scoop.<span class="price">EL 00.00</span></div>
    <div class="dessert">Baklava with Nuts Syrup and Sugar.<span class="price">EL 00.00</span></div>
    <div class="dessert">Vanilla Ice Cream Profiterole with dark and white chocolate sauce.<span class="price">EL 00.00</span></div>
    <div class="dessert">Caramelized Banana with Deep Fried Ice Cream.<span class="price">EL 00.00</span></div>
    <div class="dessert">Shot Glass Sampler Tiramisu, Chocolate Crisp Mousse, Pear with Sabayon.<span class="price">EL 00.00</span></div>
  </div>
  <div class="brand" style="left:730px;top:545px;width:85px;font-size:13px">Meadowlark</div>
</section>

</body>
</html>
```